Stonebrace Business Card Design

The Stonebrace Co is an aggregate (crushing) equipment dealer serving Western Canadian provinces. Stonebrace is a distributor of aggregate equipment for different manufacturers.

We are looking to change and update the existing business card which has been used since the existence of the company. A copy of existing card has been attached for reference. The Stonebrace Co logo we want to remain the same and we want the green color to remain the same.

We are wanting something new with a different look. A refreshing card to show a new modern and updated look. No longer wanting to have the manufacturers on the back of the card but something more like our logo on the back of the card with a statement like "Crushing Solutions"

ideas could be:
- card can be different colors on front and back
- front or reverse of the card could possibly be the green color with the logo in black

Target Market(s)

Owners of Aggregate/Crushing companies

Contact Information for Business Card

see above

Requirements
Must have
• - logo to remain same along with same font within logo
• - green color to remain same
Nice to have
• as noted above under project description
Should not have

```html
<!DOCTYPE html>
<html lang="en">
<head>
<meta charset="utf-8">
<title>Stonebrace Business Card</title>
<link rel="stylesheet" href="https://fonts.googleapis.com/css2?family=Roboto:wght@400;500;700&family=Roboto+Condensed:wght@500;700&display=swap">
<style>
  :root {
    --brand-green: #878b0c;
    --brand-green-text: #8a8c10;
    --ink: #1f1d1b;
    --body-text: #4a4a4a;
    --card-white: #f6f6f4;
    --backdrop: #7a5a42;
  }
  * { margin: 0; padding: 0; box-sizing: border-box; }
  html, body { width: 1200px; height: 960px; overflow: hidden; }
  body {
    background: var(--backdrop);
    position: relative;
    font-family: "Roboto", Arial, sans-serif;
  }
  .card {
    position: absolute;
    left: 320px;
    width: 600px;
    height: 342px;
    border-radius: 22px;
  }
  .card--front {
    top: 108px;
    background: var(--brand-green);
  }
  .front-brand {
    position: absolute;
    left: 0; right: 0;
    top: 152px;
    display: flex;
    justify-content: center;
    align-items: center;
    gap: 18px;
  }
  .front-brand .brand-dot {
    width: 40px; height: 40px;
    border-radius: 50%;
    background: var(--ink);
  }
  .front-brand .brand-name {
    font-family: "Roboto", Arial, sans-serif;
    font-weight: 700;
    font-size: 23px;
    letter-spacing: 0.2px;
    color: var(--ink);
  }
  .card--back {
    top: 493px;
    background: var(--card-white);
    text-align: center;
  }
  .back-brand {
    margin-top: 76px;
    display: flex;
    justify-content: center;
    align-items: center;
    gap: 10px;
    height: 40px;
  }
  .back-brand .brand-dot {
    width: 22px; height: 22px;
    border-radius: 50%;
    background: var(--brand-green-text);
  }
  .back-brand .brand-name {
    font-weight: 700;
    font-size: 17px;
    color: var(--brand-green-text);
    letter-spacing: 0.5px;
  }
  .person-name {
    margin-top: 14px;
    font-family: "Roboto Condensed", "Arial Narrow", sans-serif;
    font-weight: 500;
    font-size: 22px;
    line-height: 24px;
    color: var(--brand-green-text);
  }
  .person-title {
    font-size: 14px;
    line-height: 20px;
    color: var(--ink);
    letter-spacing: 0.3px;
  }
  .contact {
    margin-top: 8px;
    font-size: 14px;
    line-height: 21px;
    color: var(--body-text);
  }
  .contact .label { color: var(--brand-green-text); }
  .tagline {
    margin-top: 4px;
    font-weight: 500;
    font-size: 14.5px;
    color: var(--brand-green-text);
  }
</style>
</head>
<body>
  <section class="card card--front" aria-label="Business card front">
    <div class="front-brand">
      <span class="brand-dot"></span>
      <span class="brand-name">THE STONEBRACE CO.</span>
    </div>
  </section>

  <section class="card card--back" aria-label="Business card back">
    <div class="back-brand">
      <span class="brand-dot"></span>
      <span class="brand-name">STONEBRACE</span>
    </div>
    <h1 class="person-name">DALE MARSTEN</h1>
    <p class="person-title">CEO/FOUNDER</p>
    <div class="contact">
      <p>5820- 72B Street, Ridgeford, Alberta T4R 2M6</p>
      <p><span class="label">P.</span> 587.555.0142 <span class="label">M.</span> 587.555.0178 <span class="label">F.</span> 587.555.0193</p>
      <p><span class="label">E.</span> dale@stonebr.com <span class="label">W.</span> www.stonebrace.ca</p>
    </div>
    <p class="tagline">Crushing Solutions</p>
  </section>
</body>
</html>
```